Garden Design Flier

I would like a PDF of this half page A4 flier in soft green tones with dark green leaves.

Target Market(s)

Home owners and real estate agents

Font styles to use
Serif
Other font styles liked:
• Papyrus

Colors
acd136
9bcb3c
cadf82
fefdec

Requirements
Must have
• Green tones
Nice to have
• Leaves, vines, lawns
Should not have
• Open to ideas, but classic style

```html
<!DOCTYPE html>
<html lang="en">
<head>
<meta charset="utf-8">
<title>Verdant Plots – Garden Design Flier</title>
<link rel="stylesheet" href="https://fonts.googleapis.com/css2?family=Open+Sans:wght@400;700&display=swap">
<style>
  :root {
    --backdrop: #414143;
    --paper: #ffffff;
    --lawn-light: #4f9a2e;
    --lawn-mid: #2f7a26;
    --lawn-deep: #164a19;
    --leaf-light: #b9dc7a;
    --badge: rgba(14, 74, 40, 0.85);
    --slogan: #808084;
    --body-ink: #2d2d2f;
    --contact-ink: #47474a;
    --accent: #1fb39a;
    --white: #ffffff;
  }
  * { box-sizing: border-box; margin: 0; padding: 0; }
  html, body {
    width: 1200px; height: 1200px; overflow: hidden;
    background: var(--backdrop);
    font-family: "Open Sans", Arial, sans-serif;
  }
  .flier {
    position: absolute; left: 67px; top: 224px;
    width: 1066px; height: 751px;
    background: var(--paper);
  }
  .hero {
    position: absolute; left: 0; top: 0; width: 1066px; height: 472px;
    background:
      radial-gradient(ellipse 70% 30% at 45% 0%, var(--leaf-light) 0%, rgba(185,220,122,0) 100%),
      radial-gradient(ellipse 60% 70% at 50% 55%, var(--lawn-light) 0%, var(--lawn-mid) 55%, var(--lawn-deep) 100%);
  }
  .brand {
    position: absolute; left: 0; right: 0; top: 245px;
    text-align: center; color: var(--white);
    font-weight: 700; line-height: 1;
  }
  .brand-main { display: block; font-size: 78px; letter-spacing: 1px; }
  .brand-sub { display: block; font-size: 34px; letter-spacing: 14px; margin-top: 14px; padding-left: 14px; }
  .maker {
    position: absolute; left: 823px; top: 408px; width: 218px; height: 48px;
    background: var(--badge); color: var(--white);
    padding: 2px 0 0 12px;
  }
  .maker-name { font-size: 23px; line-height: 28px; }
  .maker-cred { font-size: 10.5px; line-height: 14px; }
  .services {
    position: absolute; left: 0; right: 0; top: 480px;
    display: flex; justify-content: center; gap: 29px;
    font-weight: 700; font-size: 38px; color: var(--slogan); line-height: 52px;
  }
  .pitch {
    position: absolute; left: 0; right: 0; top: 568px;
    text-align: center; font-size: 21px; line-height: 32px; color: var(--body-ink);
  }
  .contact {
    position: absolute; top: 665px; width: 240px; margin-left: -120px;
    text-align: center; color: var(--contact-ink); font-size: 15.5px;
  }
  .contact-icon { display: block; margin: 0 auto 6px; width: 33px; height: 33px; }
  .contact-label { display: block; font-weight: 700; color: var(--accent); font-size: 21px; line-height: 26px; margin: 9px 0 4px; }
  .contact-email { left: 309px; }
  .contact-phone { left: 533px; }
  .contact-abn { left: 740px; }
</style>
</head>
<body>
  <main class="flier">
    <section class="hero" role="img" aria-label="Photograph of a lush green lawn with trailing ivy leaves along the top and clover near the bottom edge">
      <h1 class="brand"><span class="brand-main">VERDANT</span><span class="brand-sub">PLOTS</span></h1>
      <div class="maker">
        <p class="maker-name">by Liam Hartley</p>
        <p class="maker-cred">Certificate 3. Horticulture Greenfield Institute</p>
      </div>
    </section>

    <p class="services"><span>DESIGN</span><span>INSTALL</span><span>GROW</span><span>TEND</span><span>ENJOY</span></p>

    <p class="pitch">All your gardening and landscaping needs from design and installation to general maintenance<br>Bespoke vegetables gardens and potager designs created to suite your site and requirements.</p>

    <div class="contact contact-email">
      <svg class="contact-icon" viewBox="0 0 33 33" aria-hidden="true">
        <circle cx="16.5" cy="16.5" r="16.5" fill="var(--accent)"/>
        <rect x="8" y="10.5" width="17" height="12" fill="none" stroke="#fff" stroke-width="1.6"/>
        <path d="M8 10.5 L16.5 17.5 L25 10.5 M8 22.5 L14 16 M25 22.5 L19 16" fill="none" stroke="#fff" stroke-width="1.6"/>
      </svg>
      liam@verdantplots.com.au
    </div>
    <div class="contact contact-phone">
      <svg class="contact-icon" viewBox="0 0 33 33" aria-hidden="true">
        <circle cx="16.5" cy="16.5" r="16.5" fill="var(--accent)"/>
        <circle cx="16.5" cy="16.5" r="10" fill="none" stroke="#fff" stroke-width="1.6"/>
        <path d="M12.5 20.5 c2 2 4 2.5 5.5 1.5 l1.2-1.5 -2-1.8 -1.3 1 c-1-.5-2-1.5-2.5-2.5 l1-1.3 -1.8-2 -1.5 1.2 c-1 1.5-.5 3.5 1.4 5.4z" fill="#fff"/>
      </svg>
      0400-183265
    </div>
    <div class="contact contact-abn">
      <span class="contact-label">ABN</span>
      12345678901
    </div>
  </main>
</body>
</html>
```